GivingGavelHub Website Redesign

I'm looking to give our website a new look and feel with better graphics/images and that is focused on conversions.
www.givinggavelhub.example. The content can stay the same. Im looking for a new hero section with maybe a call to auction form to create an auction by asking for the following information: Event Name, Event Benefits, Country, Time zone and currency.
Our goal is to show that we can host online auctions, mobile auctions and live in-person auction. The content does not need to change on the site. We just need sections or illustrations that represent those features. It would also be good to have a sections that will segment our users into the following categories: Nonprofits/Charities, Schools/Education, Businesses, Government Agency, Individual.
The following pages need to be updated:
https://www.givinggavelhub.example/
https://www.givinggavelhub.example/online-bidding-features
https://www.givinggavelhub.example/online-bidding-experience
https://www.givinggavelhub.example/about
https://www.givinggavelhub.example/pricing
Updates
This project would cover the following 4 pages:
https://www.givinggavelhub.example

```html
<!DOCTYPE html>
<html lang="en">
<head>
<meta charset="utf-8">
<title>GivingGavelHub – Online Charity Auctions</title>
<link href="https://fonts.googleapis.com/css2?family=Poppins:wght@400;500;600;700&display=swap" rel="stylesheet">
<style>
:root{
  --navy:#0b3a98;
  --blue:#1f5fd0;
  --sky:#3b8cf2;
  --pale:#d8e8fb;
  --paler:#eef5fe;
  --red:#e5352b;
  --ink:#1d1f27;
  --text:#3a3d48;
  --muted:#8b93a3;
  --white:#ffffff;
  --footer:#1f2025;
}
*{box-sizing:border-box;margin:0;padding:0}
html,body{width:1200px;height:4422px;overflow:hidden}
body{position:relative;font-family:"Poppins",sans-serif;color:var(--text);
  background:linear-gradient(180deg,#eaf3fe 0,#d4e6fb 700px,#d6e7fb 1000px,#eaf3fe 1400px,#ffffff 1560px,#ffffff 3650px,#ddeafb 3800px,#ffffff 4107px)}
.abs{position:absolute}
a{color:inherit;text-decoration:none}

/* header */
.logo{display:flex;align-items:center;gap:12px;font-weight:600;font-size:29px;color:var(--navy);letter-spacing:-.5px}
.logo-dot{width:44px;height:44px;border-radius:50%;background:var(--sky)}
.site-logo{left:112px;top:30px}
.nav{left:601px;top:40px;font-size:15px;color:var(--ink)}
.nav a{position:absolute;white-space:nowrap}
.btn{display:inline-flex;align-items:center;justify-content:center;border-radius:30px;font-size:14px;font-weight:500;white-space:nowrap}
.btn-red{background:var(--red);color:var(--white)}
.btn-outline{border:2px solid var(--red);color:var(--red);background:var(--white)}
.signin{left:930px;top:33px;width:97px;height:37px}
.search{left:1049px;top:33px;width:37px;height:37px;border-radius:50%;background:var(--blue)}

/* hero form */
.create-card{left:112px;top:144px;width:437px;height:374px;border-radius:6px;
  background:linear-gradient(180deg,#4192f4,#1e63d3);box-shadow:0 10px 30px rgba(20,70,160,.2)}
.create-card h2{position:absolute;left:0;right:0;top:26px;text-align:center;color:var(--white);font-weight:500;font-size:25px}
.field{position:absolute;background:var(--white);border-radius:4px;height:43px;font-size:12px;color:#444;display:flex;align-items:center;padding-left:14px}
.field.select::after{content:"";position:absolute;right:16px;top:16px;width:6px;height:6px;border-right:1.5px solid #666;border-bottom:1.5px solid #666;transform:rotate(45deg)}
.submit{left:170px;top:307px;width:96px;height:34px;font-size:13px}
.hero-title{left:596px;top:200px;width:560px;font-size:44px;line-height:55px;font-weight:700;color:var(--navy);letter-spacing:-.3px}
.hero-title .hl{color:var(--sky)}
.how{left:596px;top:390px;width:163px;height:37px;font-size:13px}

/* categories */
.cat-title{left:112px;top:624px;font-size:38px;line-height:46px;font-weight:700;color:var(--navy)}
.cat-title span{color:var(--sky)}
.cat-rule{left:112px;top:731px;width:115px;height:4px;background:var(--navy)}
.cat{width:192px;height:192px;border-radius:50%;top:598px;display:flex;align-items:center;justify-content:center;text-align:center;color:var(--white);font-size:18px;line-height:30px;box-shadow:0 8px 16px rgba(0,0,0,.25)}
.arrow-btn{width:44px;height:32px;border-radius:16px}
.arr-red{background:#f3c7c9}
.arr-grey{background:#cfd6e0}

/* section headings */
.sec-head{left:0;width:1200px;text-align:center;font-weight:700;line-height:46px;font-size:39px;color:var(--navy)}
.sec-head .hl{color:var(--sky)}
.rule{height:4px;width:115px;background:var(--navy);left:542px}

/* slider */
.feat-icon{left:112px;top:1152px;width:70px;height:70px;border-radius:50%;background:#bfd9fa;border:2px solid #80b4f4}
.slide-title{left:116px;top:1248px;font-size:21px;font-weight:600;color:var(--ink)}
.slide-text{left:116px;top:1290px;width:460px;font-size:15px;line-height:30px}
.slide-link{left:116px;top:1398px;font-size:16px;font-weight:600;color:var(--red)}
.slide-photo{left:666px;top:1125px;width:424px;height:370px;border-radius:18px;background:linear-gradient(150deg,#8fb8ee,#3f76c9)}

/* steps */
.step-ico{width:86px;height:86px;border-radius:50%;background:var(--white);box-shadow:0 6px 16px rgba(30,80,170,.15);top:1803px}
.step-title{top:1911px;font-size:19px;font-weight:500;color:var(--ink)}
.step-text{top:1943px;width:275px;font-size:14.5px;line-height:30px}

/* host */
.host-card{top:2433px;width:318px;height:266px;background:var(--white);border-radius:6px;overflow:hidden}
.host-card .ph{height:205px}
.host-card p{text-align:center;font-size:19px;color:var(--ink);margin-top:18px}

/* features */
.f-item{font-size:11px;line-height:20.5px;color:#555}
.f-item h4{font-size:13.5px;font-weight:600;color:var(--navy);letter-spacing:.3px;margin-bottom:7px}
.f-left{text-align:right}
.f-ico{width:82px;height:82px;border-radius:50%;background:var(--white);box-shadow:0 6px 16px rgba(30,80,170,.2)}

/* footer */
.footer{left:0;top:4107px;width:1200px;height:315px;background:var(--footer)}
.foot-links{left:0;width:1200px;top:4300px;text-align:center;font-size:15.5px;color:#e7e7ea}
.foot-links a{margin:0 11px}
.social{top:4350px;width:22px;height:22px;border-radius:50%;background:#fff}
.copy{left:0;width:1200px;top:4394px;text-align:center;font-size:13px;color:#8e909a}
</style>
</head>
<body>

<!-- header -->
<div class="abs logo site-logo"><span class="logo-dot"></span>GivingGavelHub</div>
<nav class="abs nav">
  <a style="left:0">How It Works</a>
  <a style="left:122px">Pricing</a>
  <a style="left:199px">About</a>
  <a style="left:270px">Blog</a>
</nav>
<a class="abs btn btn-red signin">Sign in</a>
<div class="abs search">
  <svg width="37" height="37" viewBox="0 0 37 37"><circle cx="17" cy="17" r="6" fill="none" stroke="#fff" stroke-width="2"/><path d="M21.5 21.5l4 4" stroke="#fff" stroke-width="2"/></svg>
</div>

<!-- hero -->
<form class="abs create-card">
  <h2>Create an Auction</h2>
  <div class="field" style="left:25px;top:82px;width:385px">Event Name</div>
  <div class="field" style="left:25px;top:137px;width:385px">Event Benefits</div>
  <div class="field select" style="left:25px;top:192px;width:188px">Country</div>
  <div class="field select" style="left:222px;top:192px;width:188px">Time zone</div>
  <div class="field select" style="left:25px;top:247px;width:385px">Currency</div>
  <span class="abs btn btn-red submit">Submit</span>
</form>
<h1 class="abs hero-title">You’ve just found the <span class="hl">easiest online auction platform</span> to use, period.</h1>
<a class="abs btn btn-outline how">How It Works&nbsp;&nbsp;<svg width="10" height="12" viewBox="0 0 10 12"><path d="M1 1l8 5-8 5z" fill="#e5352b"/></svg></a>

<!-- categories -->
<h2 class="abs cat-title"><span>Our</span><br>Categories</h2>
<div class="abs cat-rule"></div>
<div class="abs cat" style="left:386px;background:linear-gradient(160deg,#7d8a70,#3c3f3a)" role="img" aria-label="Volunteers working together at a charity">Nonprofits/<br>Charities</div>
<div class="abs cat" style="left:642px;background:linear-gradient(160deg,#9b6a4c,#3e2b22)" role="img" aria-label="Students in a classroom">Schools/<br>Education</div>
<div class="abs cat" style="left:898px;background:linear-gradient(160deg,#58606d,#262b33)" role="img" aria-label="Business people shaking hands">Businesses</div>
<div class="abs arrow-btn arr-red" style="left:1125px;top:656px"><svg width="44" height="32"><path d="M12 16h22M27 10l7 6-7 6" stroke="#e5352b" stroke-width="2" fill="none"/></svg></div>
<div class="abs arrow-btn arr-grey" style="left:1125px;top:708px"><svg width="44" height="32"><path d="M32 16H10M17 10l-7 6 7 6" stroke="#555" stroke-width="2" fill="none"/></svg></div>

<!-- wave 1 -->
<svg class="abs" style="left:0;top:800px" width="1200" height="180" viewBox="0 0 1200 180">
  <path d="M0 70C120 20 230 20 360 60S620 110 760 70 1030 20 1200 60V90C1040 60 900 80 760 110S500 120 360 95 120 70 0 160Z" fill="#0f49b3"/>
  <path d="M0 160C120 70 240 80 360 98S600 130 760 112 1040 60 1200 90V100C1050 80 900 110 760 128S500 140 360 115 110 100 0 180Z" fill="#6aa8f5" opacity=".5"/>
</svg>

<!-- spend less time -->
<h2 class="abs sec-head" style="top:980px"><span class="hl">Spend less time.</span><br>Make more money.</h2>
<div class="abs feat-icon"><svg width="66" height="66"><circle cx="36" cy="37" r="14" fill="none" stroke="#1f5fd0" stroke-width="2"/><path d="M36 37V29M33 20h6M14 33h10M16 39h8" stroke="#1f5fd0" stroke-width="2"/></svg></div>
<h3 class="abs slide-title">Quickly create, design &amp; manage auctions.</h3>
<p class="abs slide-text">You are only 5 minutes away from having your auction built and ready for items. We took the pain and confusion out of getting started.</p>
<a class="abs slide-link">Build An Auction &nbsp;→</a>
<div class="abs arrow-btn arr-grey" style="left:32px;top:1280px"><svg width="44" height="32"><path d="M32 16H10M17 10l-7 6 7 6" stroke="#555" stroke-width="2" fill="none"/></svg></div>
<div class="abs arrow-btn arr-red" style="left:1125px;top:1280px"><svg width="44" height="32"><path d="M12 16h22M27 10l7 6-7 6" stroke="#e5352b" stroke-width="2" fill="none"/></svg></div>
<div class="abs slide-photo" role="img" aria-label="Excited man celebrating while looking at his phone"></div>

<!-- build -->
<h2 class="abs sec-head" style="top:1590px"><span class="hl">Build your auction</span><br>in minutes, not days.</h2>
<div class="abs rule" style="top:1693px"></div>
<p class="abs" style="left:0;width:1200px;top:1731px;text-align:center;font-size:17px;color:var(--ink)">Three steps is all it takes to have your auction up in as little as 5 minutes.</p>
<svg class="abs" style="left:190px;top:1800px" width="1010" height="80"><path d="M20 40C120 70 200 70 300 55S460 30 560 32 700 70 800 62 950 30 1010 30" fill="none" stroke="#b8c4d6" stroke-width="1.5" stroke-dasharray="6 5"/></svg>
<div class="abs step-ico" style="left:112px"><svg width="86" height="86"><rect x="28" y="28" width="30" height="30" rx="3" fill="none" stroke="#1f5fd0" stroke-width="2"/><path d="M28 35h30" stroke="#1f5fd0" stroke-width="2"/></svg></div>
<div class="abs step-ico" style="left:472px"><svg width="86" height="86"><rect x="26" y="30" width="30" height="24" rx="3" fill="none" stroke="#1f5fd0" stroke-width="2"/><path d="M29 50l8-9 6 6 5-4 6 7" stroke="#1f5fd0" stroke-width="2" fill="none"/><circle cx="57" cy="54" r="6" fill="#fff" stroke="#1f5fd0" stroke-width="2"/></svg></div>
<div class="abs step-ico" style="left:833px"><svg width="86" height="86"><circle cx="32" cy="44" r="6" fill="none" stroke="#1f5fd0" stroke-width="2"/><circle cx="52" cy="34" r="6" fill="none" stroke="#1f5fd0" stroke-width="2"/><circle cx="52" cy="54" r="6" fill="none" stroke="#1f5fd0" stroke-width="2"/></svg></div>
<h4 class="abs step-title" style="left:112px">Build</h4>
<h4 class="abs step-title" style="left:474px">Add</h4>
<h4 class="abs step-title" style="left:835px">Share</h4>
<p class="abs step-text" style="left:112px">Answer a few questions about your event and your auction will be ready to populate with items in less than 5 minutes.</p>
<p class="abs step-text" style="left:474px">Upload items in bulk or add them one at a time. Our item wizard will walk you through the process.</p>
<p class="abs step-text" style="left:835px">When you are ready to go live, share your auction’s custom URL through email, social media, &amp; your website.</p>
<a class="abs btn btn-red" style="left:473px;top:2068px;width:255px;height:35px;font-size:13.5px">I’m ready to build my auction</a>

<!-- we host -->
<svg class="abs" style="left:0;top:2190px" width="1200" height="640" viewBox="0 0 1200 640">
  <path d="M0 60C200 110 360 100 560 60S960 0 1200 50V560C1000 520 820 610 600 610S180 520 0 620Z" fill="#0f47b0"/>
  <path d="M0 60C200 110 360 100 560 60S960 0 1200 50V120C980 60 820 140 620 140S200 60 0 160Z" fill="#5c9df3" opacity=".55"/>
  <path d="M0 520C220 460 420 580 640 540S1000 470 1200 520V560C1000 520 820 610 600 610S180 520 0 620Z" fill="#3a7ee8" opacity=".6"/>
</svg>
<h2 class="abs sec-head" style="top:2304px;color:var(--white)">We Host</h2>
<div class="abs" style="left:551px;top:2373px;width:97px;height:3px;background:#fff"></div>
<div class="abs host-card" style="left:112px"><div class="ph" role="img" aria-label="Woman cheering in front of her laptop" style="background:linear-gradient(160deg,#c7c9c2,#8f938b)"></div><p>Online Auctions</p></div>
<div class="abs host-card" style="left:443px"><div class="ph" role="img" aria-label="Couple celebrating while looking at a phone" style="background:linear-gradient(160deg,#d2c8bc,#958a7d)"></div><p>Mobile Auctions</p></div>
<div class="abs host-card" style="left:773px"><div class="ph" role="img" aria-label="Auctioneer at a podium with bidders raising paddles" style="background:linear-gradient(160deg,#c9ccd2,#6e7480)"></div><p>Live In-person Auctions</p></div>

<!-- features -->
<h2 class="abs sec-head" style="top:2902px"><span class="hl">Every Charity Auction comes<br>packed with all the features you</span><br>need to run a live event too.</h2>
<div class="abs" style="left:292px;top:3168px;width:601px;height:360px;border-radius:300px 300px 0 0;border:6px solid #d8e8fb;background:linear-gradient(180deg,#f1f0ee,#d9d6d1)" role="img" aria-label="Laptop on a desk showing the auction dashboard"></div>

<div class="abs f-item f-left" style="left:170px;top:3118px;width:260px"><h4>PRE-REGISTER GUESTS</h4>When you pre-register your guests, this gets everyone set up for the auction before it begins. Pre-register guests and let them start bidding as soon as they get a ticket.</div>
<div class="abs f-item f-left" style="left:60px;top:3256px;width:240px"><h4>ATTENDEE MANAGEMENT</h4>Manage your attendee communications via your GivingGavelHub dashboard. Our donor management system works for you so you can raise more funds, and help more people.</div>
<div class="abs f-item f-left" style="left:18px;top:3402px;width:240px"><h4>ACCEPT DONATIONS</h4>We have integrated payment systems so you can accept donations via credit card, check, PayNest, and more.</div>
<div class="abs f-item" style="left:735px;top:3118px;width:250px"><h4>FAST CHECK OUT</h4>You can manage your entire auction from anywhere in the world. Our cloud based platform lets you and unlimited volunteers login from anywhere to help you manage the auction.</div>
<div class="abs f-item" style="left:864px;top:3254px;width:250px"><h4>LIVE EVENT BIDDING</h4>Raise more money at your live event when you ditch the old paper bid sheets and move to mobile. You’ll raise more money with mobile bidding.</div>
<div class="abs f-item" style="left:932px;top:3400px;width:250px"><h4>SELL EVENT TICKETS</h4>Sell tickets to your next gala or event and put everything on auto pilot. Pre-register guests for the auction and even let them start bidding as soon as they buy a ticket.</div>

<div class="abs f-ico" style="left:443px;top:3196px"><svg width="82" height="82"><rect x="28" y="24" width="24" height="32" rx="3" fill="none" stroke="#1f5fd0" stroke-width="2"/><circle cx="52" cy="52" r="8" fill="#fff" stroke="#1f5fd0" stroke-width="2"/><path d="M48 52l3 3 5-5" stroke="#1f5fd0" stroke-width="2" fill="none"/></svg></div>
<div class="abs f-ico" style="left:331px;top:3264px"><svg width="82" height="82"><rect x="34" y="20" width="14" height="18" fill="none" stroke="#1f5fd0" stroke-width="2"/><path d="M22 56h40M26 50a4 4 0 018 0M38 50a4 4 0 018 0M50 50a4 4 0 018 0" stroke="#1f5fd0" stroke-width="2" fill="none"/></svg></div>
<div class="abs f-ico" style="left:282px;top:3419px"><svg width="82" height="82"><rect x="34" y="40" width="26" height="18" fill="none" stroke="#1f5fd0" stroke-width="2"/><path d="M22 28l14 12M38 48h14" stroke="#1f5fd0" stroke-width="2"/></svg></div>
<div class="abs f-ico" style="left:632px;top:3196px"><svg width="82" height="82"><path d="M42 26H28v30h14M36 41h22M52 35l6 6-6 6" stroke="#1f5fd0" stroke-width="2" fill="none"/></svg></div>
<div class="abs f-ico" style="left:757px;top:3264px"><svg width="82" height="82"><path d="M30 28l12 12M40 24l12 12M36 32l-8 8M34 38l16 16M24 58h26" stroke="#1f5fd0" stroke-width="2" fill="none"/></svg></div>
<div class="abs f-ico" style="left:826px;top:3419px"><svg width="82" height="82"><path d="M20 32h42v6a5 5 0 000 10v6H20v-6a5 5 0 000-10z" fill="none" stroke="#1f5fd0" stroke-width="2"/><path d="M41 37l2 5h5l-4 3 2 5-5-3-5 3 2-5-4-3h5z" fill="none" stroke="#1f5fd0" stroke-width="1.5"/></svg></div>

<a class="abs btn btn-red" style="left:373px;top:3563px;width:215px;height:36px;font-size:13.5px">I’m ready to get started</a>
<a class="abs btn btn-outline" style="left:612px;top:3563px;width:216px;height:36px;font-size:13.5px">Schedule a Consultation</a>

<!-- wave 3 -->
<svg class="abs" style="left:0;top:3630px" width="1200" height="160" viewBox="0 0 1200 160">
  <path d="M0 80C200 130 400 150 640 120S1000 40 1200 0V60C1000 110 820 150 620 150S200 110 0 100Z" fill="#0f47b0"/>
  <path d="M0 100C220 120 420 160 640 150S1000 80 1200 60V80C1000 120 820 170 620 165S200 130 0 110Z" fill="#3a7ee8" opacity=".5"/>
</svg>

<!-- download -->
<div class="abs" style="left:125px;top:3830px;width:325px;height:240px;border-radius:14px;transform:rotate(-12deg);background:linear-gradient(150deg,#1c3f8c,#0a1a44);border:8px solid #f4f6fa;box-shadow:0 12px 24px rgba(0,0,0,.25)" role="img" aria-label="Tablet showing the Auction Growth Playbook cover"></div>
<h2 class="abs" style="left:516px;top:3846px;font-size:38px;line-height:46px;font-weight:700;color:var(--navy)"><span style="color:var(--sky)">Download the</span><br>Auction Growth Playbook™</h2>
<p class="abs" style="left:516px;top:3984px;width:590px;font-size:15px;line-height:30px;color:var(--ink)">Learn the 4 tools BIG Organizations use to skyrocket their auction profits! Stop leaving thousands of dollars on the table by following this Step-By-Step Guide.</p>
<a class="abs btn btn-red" style="left:516px;top:4069px;width:232px;height:36px;font-size:13.5px">Help me raise more money</a>

<!-- footer -->
<footer class="abs footer"></footer>
<div class="abs logo" style="left:405px;top:4222px;color:#fff;font-weight:500;font-size:30px"><span class="logo-dot" style="background:#fff"></span>GivingGavelHub</div>
<nav class="abs foot-links"><a>Home</a><a>How It Works</a><a>Pricing</a><a>About</a><a>Blog</a><a>Silent Auctions</a><a>Browse Auctions</a></nav>
<span class="abs social" style="left:542px"></span>
<span class="abs social" style="left:572px"></span>
<span class="abs social" style="left:602px"></span>
<span class="abs social" style="left:632px"></span>
<p class="abs copy">© 2023 GivingGavelHub &nbsp;- All Rights Reserved</p>
</body>
</html>
```